Card front cover, made up of words and statements, similar to the front of a tovarique bag.

I'm looking to design the front of a card or post card I will use in my business. I want to use a mash up of words and statements and sentences to inspire my audience. The card should be visually nice and use various fonts. My business inspires kids to set goals and dream big. You can use the "moon" shape as seen in my logo, but stick to mostly the words and statements listed on the attached word document or other similar statements you find, the shorter statements tend to look better. I'm interested to see a use of different fonts and sizes. All with a "modern" look and feel.

Target Market(s)

parents of children ages 8-12

Industry/Entity Type

Party space: specifically slumber parties

Font styles to use
Other font styles liked:
• Avenir Next LT pro

Colors
FFC000
F8CF3A
FAE287
FDF2CF
FEFAEE

Requirements
Must have
• The use of the "moon" logo and the words: Sleep Less, Dream More
Nice to have
• I made a long list of inspirational quotes to use, they don't all need to be used but that is the idea I'm looking for. After looking at designs the long sentences do NOT work as well. Please either shorten them or find other similar statements.
Should not have
• color, please use the yellow as shown in my moon logo, black and white

```html
<!DOCTYPE html>
<html lang="en">
<head>
<meta charset="utf-8">
<title>Sleep Less, Dream More – Card Front</title>
<link rel="stylesheet" href="https://fonts.googleapis.com/css2?family=Arimo&family=Bodoni+Moda:wght@400;700;800&family=Carlito&family=Libre+Baskerville:wght@700&family=Playfair+Display&display=swap">
<style>
  :root {
    --sun: #ffc000;
    --sun-soft: #ffd62e;
    --sun-light: #fff455;
    --ink: #333333;
    --bar: #363636;
    --paper: #ffffff;
  }
  html, body {
    margin: 0;
    width: 1200px;
    height: 926px;
    overflow: hidden;
    background: var(--paper);
  }
  .card { display: block; width: 1200px; height: 926px; }
  .ink { fill: var(--ink); }
  .on-bar { fill: var(--sun); }
  .bar { fill: var(--bar); }
  .rule { stroke: var(--ink); stroke-width: 1.3; }
  .serif-bold { font-family: "Libre Baskerville", Georgia, serif; font-weight: 700; }
  .didone-heavy { font-family: "Bodoni Moda", "Didot", serif; font-weight: 800; }
  .didone-bold { font-family: "Bodoni Moda", "Didot", serif; font-weight: 700; }
  .didone-light { font-family: "Bodoni Moda", "Didot", serif; font-weight: 400; }
  .display-serif { font-family: "Playfair Display", Georgia, serif; font-weight: 400; }
  .sans { font-family: Arimo, Arial, sans-serif; }
  .humanist { font-family: Carlito, Calibri, sans-serif; }
</style>
</head>
<body>
<svg class="card" viewBox="0 0 1200 926" xmlns="http://www.w3.org/2000/svg">
  <defs>
    <linearGradient id="sun-wash" x1="0" y1="0" x2="1" y2="1">
      <stop offset="0" stop-color="var(--sun-soft)"/>
      <stop offset="0.5" stop-color="#ffd51f"/>
      <stop offset="1" stop-color="var(--sun-light)"/>
    </linearGradient>
    <clipPath id="panel-clip"><rect x="60" y="65" width="1079" height="805"/></clipPath>
  </defs>

  <!-- panel -->
  <rect x="60" y="65" width="1079" height="805" fill="url(#sun-wash)"/>
  <g clip-path="url(#panel-clip)">
    <circle cx="505" cy="460" r="384" fill="var(--paper)" opacity="0.45"/>
  </g>

  <!-- left column -->
  <g class="serif-bold ink" font-size="30">
    <text x="90" y="128" textLength="516" lengthAdjust="spacingAndGlyphs">Never stop dreaming --- most realities</text>
    <text x="90" y="163" textLength="439" lengthAdjust="spacingAndGlyphs">were once created from dreams.</text>
  </g>

  <rect class="bar" x="88" y="191" width="504" height="38"/>
  <text class="serif-bold on-bar" x="101" y="216" font-size="12.5" textLength="474" lengthAdjust="spacingAndGlyphs">You are almost twice as likely to reach your goals simply by writing them down.</text>

  <g class="didone-heavy ink" font-size="80">
    <text x="97" y="306" textLength="494" lengthAdjust="spacingAndGlyphs">Goals are just</text>
    <text x="97" y="380" textLength="438" lengthAdjust="spacingAndGlyphs">dreams with</text>
    <text x="97" y="455" textLength="369" lengthAdjust="spacingAndGlyphs">a deadline</text>
  </g>

  <g class="sans ink" font-size="28">
    <text x="93" y="497" textLength="443" lengthAdjust="spacingAndGlyphs">What's one action I can take today</text>
    <text x="93" y="529" textLength="505" lengthAdjust="spacingAndGlyphs">to make my goal feel more achievable?</text>
  </g>

  <text class="sans ink" font-size="32" transform="translate(650 538) rotate(-90)" textLength="441" lengthAdjust="spacingAndGlyphs">Do what is right, not what is easy</text>

  <!-- right column -->
  <g class="display-serif ink" font-size="37">
    <text x="681" y="124" textLength="376" lengthAdjust="spacingAndGlyphs">DON'T FOLLOW YOUR</text>
    <text x="681" y="162" textLength="365" lengthAdjust="spacingAndGlyphs">DREAM CHASE THEM!</text>
  </g>
  <line class="rule" x1="685" y1="177" x2="1072" y2="177"/>

  <g class="humanist ink" font-size="23">
    <text x="682" y="204" textLength="355" lengthAdjust="spacingAndGlyphs">What's one action I can take today</text>
    <text x="682" y="232" textLength="391" lengthAdjust="spacingAndGlyphs">to make my goal feel more achievable?</text>
  </g>

  <g class="didone-heavy ink" font-size="70">
    <text x="687" y="302" textLength="359" lengthAdjust="spacingAndGlyphs">Sleep Less,</text>
    <text x="687" y="363" textLength="384" lengthAdjust="spacingAndGlyphs">Dream More</text>
  </g>
  <line class="rule" x1="687" y1="375" x2="1071" y2="375"/>

  <text class="didone-light ink" x="690" y="416" font-size="44" textLength="388" lengthAdjust="spacingAndGlyphs">Dream it, wish it, do it</text>

  <rect class="bar" x="677" y="431" width="400" height="35"/>
  <text class="didone-bold on-bar" x="690" y="454" font-size="17" textLength="372" lengthAdjust="spacingAndGlyphs">BE THE ENERGY YOU WANT TO ATTRACT</text>

  <g class="sans ink" font-size="28">
    <text x="686" y="504" textLength="374" lengthAdjust="spacingAndGlyphs">What motivates you to keep</text>
    <text x="686" y="537" textLength="395" lengthAdjust="spacingAndGlyphs">going when things get tough?</text>
  </g>

  <text class="display-serif ink" font-size="29" transform="translate(1091 103) rotate(90)" textLength="434" lengthAdjust="spacingAndGlyphs">Don't follow your dream chase them!</text>

  <!-- lower block -->
  <g class="didone-heavy ink" font-size="68">
    <text x="94" y="614" textLength="366" lengthAdjust="spacingAndGlyphs">Don't follow</text>
    <text x="94" y="688" textLength="364" lengthAdjust="spacingAndGlyphs">your dream</text>
    <text x="94" y="761" textLength="363" lengthAdjust="spacingAndGlyphs">chase them!</text>
  </g>

  <g class="serif-bold ink" font-size="28">
    <text x="504" y="590" textLength="420" lengthAdjust="spacing">A dream is not something</text>
    <text x="504" y="626" textLength="420" lengthAdjust="spacing">that happens while</text>
    <text x="504" y="662" textLength="420" lengthAdjust="spacing">you sleep, its what keeps</text>
    <text x="504" y="699" textLength="420" lengthAdjust="spacing">you awake and striving</text>
    <text x="504" y="734" textLength="420" lengthAdjust="spacing">for something greater</text>
    <text x="504" y="768" textLength="157" lengthAdjust="spacingAndGlyphs">every day</text>
  </g>

  <text class="sans ink" x="96" y="832" font-size="58" textLength="840" lengthAdjust="spacingAndGlyphs">Do what is right, not what is easy</text>

  <g class="sans ink" font-size="21">
    <text transform="translate(970 840) rotate(-90)" textLength="265" lengthAdjust="spacingAndGlyphs">What motivates you to keep</text>
    <text transform="translate(997 840) rotate(-90)" textLength="279" lengthAdjust="spacingAndGlyphs">going when things get tough?</text>
  </g>

  <rect class="bar" x="1019" y="572" width="91" height="266"/>
  <text class="didone-heavy on-bar" font-size="46" transform="translate(1075 817) rotate(-90)" textLength="227" lengthAdjust="spacingAndGlyphs">Dream More</text>
</svg>
</body>
</html>
```